Small Business Broker Business Card Design

A business card design for a small business brokerage, which is a financial service, not unlike real estate brokerage, but for small businesses such as laundromats, pizza shops, restaurants, cleaners etc. The designs should all be simple, more conservative in nature, using the colors and font of the logo. Again, think real estate Brokerage as a business context
Contact Information for Business Card
Name: Glen R. Harlow. Title: Small Business Advisor. Email: g.harlow@bayfieldcapitalworks.example. Mobile: (555) 274-3918. Office: (555) 806-2147. www.bayfieldcapitalworks.example

```html
<!DOCTYPE html>
<html lang="en">
<head>
<meta charset="utf-8">
<title>Bayfield Capital Works – Business Card</title>
<link rel="stylesheet" href="https://fonts.googleapis.com/css2?family=Montserrat:wght@400;700;800&display=swap">
<style>
  :root {
    --navy: #1b3a6b;
    --navy-light: #25477c;
    --green: #8dc63f;
    --white: #ffffff;
    --backdrop: #262626;
  }
  * { margin: 0; padding: 0; box-sizing: border-box; }
  html, body { width: 1200px; height: 900px; overflow: hidden; }
  body {
    background: var(--backdrop);
    font-family: "Montserrat", Arial, sans-serif;
    position: relative;
  }
  .card {
    position: absolute;
    left: 250px;
    width: 700px;
    height: 400px;
    background: var(--navy);
    border-bottom: 7px solid var(--green);
    overflow: hidden;
    color: var(--white);
  }
  .card--front { top: 40px; }
  .card--back { top: 470px; }
  .card__bands { position: absolute; inset: 0; width: 100%; height: 100%; }

  .brand-row { display: flex; align-items: center; gap: 14px; }
  .brand-mark { background: var(--green); flex: none; }
  .brand-name {
    font-weight: 700;
    text-transform: uppercase;
    letter-spacing: 0.03em;
    color: var(--white);
    white-space: nowrap;
  }
  .brand-tagline {
    font-weight: 700;
    text-transform: uppercase;
    letter-spacing: 0.08em;
    color: var(--green);
    white-space: nowrap;
  }

  .front-brand {
    position: absolute;
    inset: 0;
    display: flex;
    flex-direction: column;
    align-items: center;
    justify-content: center;
    gap: 12px;
  }
  .front-brand .brand-mark { width: 20px; height: 20px; }
  .front-brand .brand-name { font-size: 28px; }
  .front-brand .brand-tagline { font-size: 15px; }

  .back-brand {
    position: absolute;
    left: 32px;
    top: 168px;
    width: 310px;
  }
  .back-brand .brand-row { gap: 10px; margin-bottom: 8px; }
  .back-brand .brand-mark { width: 13px; height: 13px; }
  .back-brand .brand-name { font-size: 14px; }
  .back-brand .brand-tagline { font-size: 8.5px; letter-spacing: 0.06em; padding-left: 23px; }

  .divider {
    position: absolute;
    left: 355px;
    top: 80px;
    width: 1px;
    height: 240px;
    background: rgba(255,255,255,0.6);
  }
  .contact {
    position: absolute;
    left: 385px;
    top: 90px;
    width: 300px;
  }
  .contact__name {
    font-weight: 800;
    font-size: 26px;
    text-transform: uppercase;
    color: var(--green);
    letter-spacing: 0.02em;
  }
  .contact__title { font-size: 15px; margin-top: 4px; }
  .contact__address { font-size: 14px; margin-top: 10px; line-height: 1.45; }
  .contact__list { list-style: none; margin-top: 16px; font-size: 13px; }
  .contact__list li { display: flex; align-items: center; gap: 8px; line-height: 1.9; white-space: nowrap; }
  .contact__list svg { width: 12px; height: 12px; flex: none; fill: var(--green); }
</style>
</head>
<body>

<section class="card card--front" aria-label="Card front">
  <svg class="card__bands" viewBox="0 0 700 400" preserveAspectRatio="none" aria-hidden="true">
    <polygon points="0,40 700,0 700,70 0,120" fill="var(--navy-light)" opacity="0.7"/>
    <polygon points="0,230 700,170 700,230 0,300" fill="var(--navy-light)" opacity="0.6"/>
    <polygon points="420,0 560,0 700,260 700,400 640,400" fill="var(--navy-light)" opacity="0.45"/>
  </svg>
  <div class="front-brand">
    <div class="brand-row">
      <span class="brand-mark"></span>
      <span class="brand-name">Bayfield Capital Works, Inc</span>
    </div>
    <div class="brand-tagline">Trusted guidance for local business sales</div>
  </div>
</section>

<section class="card card--back" aria-label="Card back">
  <div class="back-brand">
    <div class="brand-row">
      <span class="brand-mark"></span>
      <span class="brand-name">Bayfield Capital Works, Inc</span>
    </div>
    <div class="brand-tagline">Trusted guidance for local business sales</div>
  </div>

  <div class="divider"></div>

  <div class="contact">
    <div class="contact__name">Glen R. Harlow</div>
    <div class="contact__title">Small Business Advisor</div>
    <div class="contact__address">P.O. Box 418 Harbor Street<br>Bayfield, WI 54814</div>
    <ul class="contact__list">
      <li>
        <svg viewBox="0 0 24 24" aria-hidden="true"><path d="M3 6c0-2 2-3 4-3l2 5-2 2c1 3 4 6 7 7l2-2 5 2c0 2-1 4-3 4C10 21 3 14 3 6z"/></svg>
        (555) 274-3918
      </li>
      <li>
        <svg viewBox="0 0 24 24" aria-hidden="true"><path d="M7 1h10a2 2 0 0 1 2 2v18a2 2 0 0 1-2 2H7a2 2 0 0 1-2-2V3a2 2 0 0 1 2-2zm0 3v14h10V4z"/></svg>
        (555) 806-2147
      </li>
      <li>
        <svg viewBox="0 0 24 24" aria-hidden="true"><path d="M2 5h20v14H2zm2 2v1l8 5 8-5V7l-8 5z"/></svg>
        g.harlow@bayfieldcapitalworks.example
      </li>
      <li>
        <svg viewBox="0 0 24 24" aria-hidden="true"><circle cx="12" cy="12" r="10" fill="none" stroke="#8dc63f" stroke-width="2"/><path d="M2 12h20M12 2c4 4 4 16 0 20M12 2c-4 4-4 16 0 20" fill="none" stroke="#8dc63f" stroke-width="1.6"/></svg>
        www.bayfieldcapitalworks.example
      </li>
    </ul>
  </div>
</section>

</body>
</html>
```